We are a local Communty Pharmacy wishing to promote and market a specialised Pharmaceutical Service

We would like a design that is professional and enticing ( according to the brief In attached files)
We wish to Market Compounding Pharmacy as a specialist side of our business.
We have the expertise a purpose built preparation laboratory.
The main purpose is an Internet presence that entices prospective patients to contact or visit our physical store.

Target Market(s)

Patients Medicos and Veterinary clients

Industry/Entity Type

Pharmacy

Coding

Coded - Design and coding required

Number of Pages Required

1 page

Requirements
Must have
• Clear friendly image
Nice to have
• soft enticing feel
Should not have
• No crass loud unprofessional elements

```html
<!DOCTYPE html>
<html lang="en">
<head>
<meta charset="utf-8">
<title>Brightwell Pharmacy – Compounding Service</title>
<link href="https://fonts.googleapis.com/css2?family=Open+Sans:wght@400;600;700&family=Raleway:wght@500;600;700&display=swap" rel="stylesheet">
<style>
:root{
  --blue:#1aa3d9;
  --blue-dark:#1487b6;
  --slate:#4d5b66;
  --orange:#f26e42;
  --ink:#3c4a55;
  --muted:#8a96a0;
  --line:#e3e8ec;
  --paper:#ffffff;
  --soft:#f4f7f9;
  --footer:#2b2f33;
  --footer-deep:#1f2225;
}
*{box-sizing:border-box;margin:0;padding:0}
html,body{width:1200px;height:2244px;overflow:hidden}
body{font-family:"Open Sans",Arial,sans-serif;color:var(--ink);background:var(--paper);font-size:14px;position:relative}
.wrap{width:1000px;margin:0 auto;position:relative}

.topbar{height:34px;border-bottom:1px solid var(--line);font-size:12px;color:var(--muted)}
.topbar .wrap{display:flex;justify-content:space-between;align-items:center;height:34px}
.topbar .contact{display:flex;gap:28px}
.topbar span{display:flex;align-items:center;gap:6px}
.topbar svg{width:12px;height:12px}

.header{height:140px}
.header .wrap{display:flex;justify-content:space-between;align-items:center;height:140px}
.brand{display:flex;align-items:center;gap:14px}
.brand .mark{width:54px;height:54px;background:var(--blue);border-radius:50%}
.brand .name{font-family:"Raleway",sans-serif;font-weight:700;font-size:30px;color:var(--blue);line-height:1;letter-spacing:.5px}
.nav{display:flex;align-items:center;gap:36px;font-family:"Raleway",sans-serif;font-size:12px;font-weight:600;color:var(--ink)}
.nav .active{color:var(--blue)}
.nav .search{width:38px;height:38px;background:var(--blue);display:flex;align-items:center;justify-content:center}

.openbar{height:54px;border-top:1px solid var(--line);border-bottom:1px solid var(--line)}
.openbar .wrap{display:flex;justify-content:space-between;align-items:center;height:54px}
.openbar .hours{display:flex;align-items:center;gap:10px;font-size:13px;font-weight:700;color:var(--ink)}
.openbar .hours small{font-weight:400;color:var(--muted);font-size:12px;margin-left:10px}
.order-btn{background:var(--blue);color:#fff;font-weight:600;font-size:14px;height:54px;width:240px;display:flex;align-items:center;justify-content:center;gap:10px}

.hero{position:relative;height:790px}
.hero .photo{position:absolute;inset:0;background:linear-gradient(120deg,#dfe9ef 0%,#c9dbe4 35%,#eef3f5 60%,#d5e4ea 100%)}
.hero .arrow{position:absolute;top:260px;width:34px;height:50px;background:rgba(255,255,255,.7);display:flex;align-items:center;justify-content:center}
.hero .arrow.left{left:0}.hero .arrow.right{right:0}
.hero-panel{position:absolute;left:100px;top:500px;width:1000px;height:250px;background:rgba(26,163,217,.88);color:#fff;display:flex}
.hero-panel .intro{width:540px;padding:30px 36px}
.hero-panel .kicker{font-size:12px;opacity:.9;display:flex;align-items:center;gap:8px}
.hero-panel h1{font-family:"Raleway",sans-serif;font-size:26px;font-weight:600;margin:6px 0 14px}
.hero-panel p{font-size:11.5px;line-height:1.6;opacity:.9;width:420px}
.ghost-btn{display:inline-block;margin-top:18px;border:1px solid #fff;border-radius:20px;padding:8px 22px;font-size:11px;font-weight:600}
.hero-panel .opening{flex:1;padding:30px 40px 0 20px;border-left:1px solid rgba(255,255,255,.3)}
.opening h2{font-family:"Raleway",sans-serif;font-size:26px;font-weight:600;display:flex;align-items:center;gap:12px;margin-bottom:16px}
.opening table{width:100%;border-collapse:collapse;font-size:11px}
.opening td{padding:7px 0;border-bottom:1px solid rgba(255,255,255,.3)}
.opening td:last-child{text-align:right}
.opening .note{font-size:11px;margin-top:10px}

.services{padding-top:50px;text-align:center}
.section-title{font-family:"Raleway",sans-serif;font-size:22px;font-weight:600;color:var(--ink)}
.section-sub{font-size:12px;color:var(--muted);margin-top:6px}
.cards{display:flex;width:1000px;margin:34px auto 0;gap:16px}
.card{flex:1;height:228px;color:#fff;padding:26px 30px;text-align:center;position:relative}
.card.blue{background:var(--blue)}.card.slate{background:var(--slate)}.card.orange{background:var(--orange)}
.card h3{font-family:"Raleway",sans-serif;font-size:12px;font-weight:700;letter-spacing:.5px;margin:12px 0 10px}
.card p{font-size:11px;line-height:1.6;opacity:.9;text-align:left}
.card .dot{position:absolute;right:22px;bottom:16px;width:8px;height:8px;background:#fff;border-radius:50%}

.about{text-align:center;padding-top:140px}
.about h2{font-family:"Raleway",sans-serif;font-size:36px;font-weight:700;color:var(--ink);letter-spacing:.5px}
.about .rule{width:60px;height:2px;background:var(--blue);margin:14px auto 30px}
.about p{width:860px;margin:0 auto 22px;font-size:12px;line-height:1.8;color:var(--muted)}
.solid-btn{display:inline-block;background:var(--blue);color:#fff;border-radius:22px;padding:11px 32px;font-size:11px;font-weight:600;margin-top:10px}

.footer{position:absolute;left:0;top:1848px;width:1200px;height:344px;background:var(--footer);color:#cfd5da}
.footer .wrap{display:flex;gap:40px;padding-top:28px}
.footer h4{font-family:"Raleway",sans-serif;font-size:12px;font-weight:700;color:#fff;letter-spacing:.5px;margin-bottom:16px}
.footer .col{flex:1}
.tweet{display:flex;gap:10px;margin-bottom:18px;font-size:10.5px;line-height:1.6}
.tweet i{flex:none;width:14px;height:14px;border-radius:50%;background:var(--blue);margin-top:2px}
.tweet b{color:var(--blue);font-weight:600}
.map{width:100%;height:170px;background:linear-gradient(135deg,#e9ebe4,#d8dccf)}
.form input,.form .area{display:block;width:100%;height:26px;background:#fff;border:0;margin-bottom:10px;font-size:10px;padding:0 8px;color:var(--muted);font-family:inherit}
.form .area{height:64px;padding-top:6px}
.form .send{float:right;background:var(--blue);color:#fff;font-size:10px;padding:7px 16px;border-radius:14px}
.bottombar{position:absolute;left:0;top:2192px;width:1200px;height:52px;background:var(--footer-deep);color:#aab2b8;font-size:11px}
.bottombar .wrap{display:flex;justify-content:space-between;align-items:center;height:52px}
.social{display:flex;align-items:center;gap:8px}
.social i{width:22px;height:22px;border-radius:50%;background:var(--blue)}
</style>
</head>
<body>

<div class="topbar">
  <div class="wrap">
    <div class="contact">
      <span><svg viewBox="0 0 24 24"><path fill="#8a96a0" d="M6.6 10.8a15 15 0 0 0 6.6 6.6l2.2-2.2c.3-.3.7-.4 1-.2 1.1.4 2.3.6 3.6.6.6 0 1 .4 1 1V20c0 .6-.4 1-1 1A17 17 0 0 1 3 4c0-.6.4-1 1-1h3.5c.6 0 1 .4 1 1 0 1.3.2 2.5.6 3.6.1.3 0 .7-.2 1z"/></svg>Tel: +00 (0)12 3456 7890</span>
      <span><svg viewBox="0 0 24 24"><path fill="#8a96a0" d="M3 5h18v14H3z M4 6l8 6 8-6"/></svg>hello@brightwellpharmacy.example</span>
    </div>
    <span>Your trusted local pharmacy and compounding lab</span>
  </div>
</div>

<header class="header">
  <div class="wrap">
    <div class="brand"><span class="mark"></span><span class="name">BRIGHTWELL<br>PHARMACY</span></div>
    <nav class="nav">
      <span class="active">HOME</span><span>ABOUT US</span><span>QUESTIONS</span><span>TIMINGS</span><span>CONTACT</span>
      <span class="search"><svg width="16" height="16" viewBox="0 0 24 24"><circle cx="10" cy="10" r="6" fill="none" stroke="#fff" stroke-width="2.5"/><path d="M15 15l5 5" stroke="#fff" stroke-width="2.5"/></svg></span>
    </nav>
  </div>
</header>

<div class="openbar">
  <div class="wrap">
    <div class="hours">
      <svg width="18" height="18" viewBox="0 0 24 24"><circle cx="12" cy="12" r="10" fill="none" stroke="#1aa3d9" stroke-width="2"/><path d="M12 6v6l4 2" stroke="#1aa3d9" stroke-width="2" fill="none"/></svg>
      OPEN 7AM TO 9PM MON ALL DAYS A WEEK !<small>Ask our pharmacists about tailored medicines made just for you</small>
    </div>
    <div class="order-btn"><svg width="16" height="16" viewBox="0 0 24 24"><path fill="#fff" d="M6.6 10.8a15 15 0 0 0 6.6 6.6l2.2-2.2c.3-.3.7-.4 1-.2 1.1.4 2.3.6 3.6.6.6 0 1 .4 1 1V20c0 .6-.4 1-1 1A17 17 0 0 1 3 4c0-.6.4-1 1-1h3.5c.6 0 1 .4 1 1 0 1.3.2 2.5.6 3.6.1.3 0 .7-.2 1z"/></svg>Make An Order Now</div>
  </div>
</div>

<section class="hero">
  <div class="photo" role="img" aria-label="Photo of a smiling pharmacist serving a customer at a bright pharmacy counter"></div>
  <div class="arrow left"><svg width="12" height="12" viewBox="0 0 12 12"><path d="M8 1L3 6l5 5" stroke="#3c4a55" stroke-width="2" fill="none"/></svg></div>
  <div class="arrow right"><svg width="12" height="12" viewBox="0 0 12 12"><path d="M4 1l5 5-5 5" stroke="#3c4a55" stroke-width="2" fill="none"/></svg></div>
  <div class="hero-panel">
    <div class="intro">
      <div class="kicker"><svg width="14" height="14" viewBox="0 0 24 24"><circle cx="12" cy="12" r="10" fill="none" stroke="#fff" stroke-width="2"/></svg>Sed quia consequuntur magni dolores</div>
      <h1>Eos qui ratione voluptatem sequi</h1>
      <p>Medicines prepared by hand in our purpose built laboratory, made to the exact strength, form and flavour each patient needs. We work closely with doctors and vets to deliver safe, tailored treatments every day.</p>
      <span class="ghost-btn">CLICK HERE</span>
    </div>
    <div class="opening">
      <h2><svg width="26" height="26" viewBox="0 0 24 24"><circle cx="12" cy="12" r="10" fill="none" stroke="#fff" stroke-width="2"/><path d="M12 6v6l4 2" stroke="#fff" stroke-width="2" fill="none"/></svg>Opening Hours</h2>
      <table>
        <tr><td>MONDAY - FRIDAY</td><td>09:00AM - 07:00PM</td></tr>
        <tr><td>SATURDAY - SUNDAY</td><td>09:00AM - 05:00PM</td></tr>
        <tr><td>EMERGENCY SERVICES</td><td>09:00AM - 09:00PM</td></tr>
      </table>
      <div class="note">24 hours opening</div>
    </div>
  </div>
</section>

<section class="services">
  <h2 class="section-title">What We Do?</h2>
  <p class="section-sub">Simple dummy text of the printing and typesetting industry, lorem ipsum has been the industry's standard dummy text.</p>
  <div class="cards">
    <div class="card blue">
      <svg width="40" height="40" viewBox="0 0 40 40"><rect x="10" y="14" width="20" height="12" rx="6" fill="none" stroke="#fff" stroke-width="2"/><path d="M20 14v12" stroke="#fff" stroke-width="2"/></svg>
      <h3>NEQUE PORRO QUISQUAM</h3>
      <p>Personal medicines prepared to order, adjusted in dose and form so patients receive exactly what their prescriber intends for safe, effective care.</p>
      <span class="dot"></span>
    </div>
    <div class="card slate">
      <svg width="40" height="40" viewBox="0 0 40 40"><rect x="10" y="14" width="20" height="12" rx="6" fill="none" stroke="#fff" stroke-width="2"/><path d="M20 14v12" stroke="#fff" stroke-width="2"/></svg>
      <h3>NEQUE PORRO QUISQUAM</h3>
      <p>We partner with local doctors and clinics, offering formulations that are not available commercially and support for tricky prescriptions.</p>
      <span class="dot"></span>
    </div>
    <div class="card orange">
      <svg width="40" height="40" viewBox="0 0 40 40"><rect x="10" y="14" width="20" height="12" rx="6" fill="none" stroke="#fff" stroke-width="2"/><path d="M20 14v12" stroke="#fff" stroke-width="2"/></svg>
      <h3>NEQUE PORRO QUISQUAM</h3>
      <p>Veterinary preparations in flavours and sizes pets accept, making daily medication easier for animals and the people who care for them.</p>
      <span class="dot"></span>
    </div>
  </div>
</section>

<section class="about">
  <h2>WHAT IS COMPOUNDING PHARMACY?</h2>
  <div class="rule"></div>
  <p>Compounding is the traditional craft of preparing medicines by hand for an individual patient. Our pharmacists combine, mix and alter ingredients to create a medicine that fits the person, removing allergens, changing strength or turning tablets into liquids, creams or treats that are easier to take each day.</p>
  <p>We are proud to offer this specialist service from our purpose built laboratory, working alongside doctors, dentists and vets. Visit our store or contact our team to discuss how a tailored preparation could help you, your family or your animals.</p>
  <span class="solid-btn">LEARN MORE</span>
</section>

<footer class="footer">
  <div class="wrap">
    <div class="col">
      <h4>RECENT TWEETS</h4>
      <div class="tweet"><i></i><div><b>@brightwellrx</b><br>New sugar free children's suspensions now available in store. Ask our team for details.<br>2 hours ago</div></div>
      <div class="tweet"><i></i><div><b>@brightwellrx</b><br>Our lab now prepares flavoured pet medicines. Talk to your vet today.<br>1 day ago</div></div>
    </div>
    <div class="col">
      <h4>OUR LOCATION</h4>
      <div class="map" role="img" aria-label="Street map showing the pharmacy location"></div>
    </div>
    <div class="col">
      <h4>OUR LOCATION</h4>
      <div class="form">
        <input value="Name*" readonly>
        <input value="E-mail*" readonly>
        <div class="area form-area" style="background:#fff;height:64px;margin-bottom:10px"></div>
        <span class="send">SEND MESSAGE</span>
      </div>
    </div>
  </div>
</footer>

<div class="bottombar">
  <div class="wrap">
    <span>Copyright © Brightwell Pharmacy 2015 | All Rights Reserved</span>
    <div class="social">Connect With Us <i></i><i></i><i></i><i></i></div>
  </div>
</div>

</body>
</html>
```